Business IT Services Billboard to attract local small businesses

We are Brivoqua, a premier Managed Service Provider (MSP) specializing in comprehensive IT services and VOIP phone solutions exclusively for businesses. Our goal is to create a dynamic and visually engaging billboard advertisement that not only highlights our cutting-edge IT solutions but also emphasizes our state-of-the-art VOIP phone services. This billboard should communicate our commitment to providing innovative, reliable, and holistic technology solutions.
See the attached supporting documentation.
Target Market(s)
small business
Industry/Entity Type
Information Technology
Colors
Designer to choose colors to be used in the design.
Look and feel
Each slider illustrates characteristics of the customer's brand and the style your logo design should communicate.

```html
<!DOCTYPE html>
<html lang="en">
<head>
<meta charset="utf-8">
<title>Brivoqua Billboard</title>
<link rel="stylesheet" href="https://fonts.googleapis.com/css2?family=Poppins:wght@300;400;700;800&display=swap">
<style>
  :root {
    --brand-blue: #1273c0;
    --ink: #000000;
    --paper: #ffffff;
    --stage: #a6a6a6;
    --rule: #8a8a8a;
    --photo-light: #f1eee8;
    --photo-mid: #d9c9ad;
    --photo-cool: #b9c8d8;
  }
  html, body {
    margin: 0;
    padding: 0;
    width: 1200px;
    height: 1200px;
    overflow: hidden;
    background: var(--stage);
    font-family: "Poppins", sans-serif;
  }
  .billboard {
    position: absolute;
    left: 40px;
    top: 320px;
    width: 1383px;
    height: 690px;
    transform: scale(0.81);
    transform-origin: top left;
    background: var(--paper);
    box-shadow: 0 4px 10px rgba(0,0,0,0.35);
    overflow: hidden;
  }
  .billboard-shapes {
    position: absolute;
    inset: 0;
    width: 1383px;
    height: 690px;
  }
  .brand-name {
    position: absolute;
    left: 86px;
    top: 52px;
    margin: 0;
    font-weight: 800;
    font-size: 56px;
    line-height: 1;
    letter-spacing: 2px;
    text-transform: uppercase;
    color: var(--brand-blue);
  }
  .headline {
    position: absolute;
    left: 86px;
    top: 180px;
    margin: 0;
    font-size: 70px;
    line-height: 62px;
    color: var(--paper);
    text-transform: uppercase;
  }
  .headline span { display: block; }
  .headline .light { font-weight: 300; letter-spacing: -1px; }
  .headline .bold { font-weight: 700; }
  .headline .accent { color: var(--brand-blue); }
  .tagline {
    position: absolute;
    left: 86px;
    top: 578px;
    margin: 0;
    font-size: 28px;
    font-weight: 400;
    line-height: 36px;
    color: var(--paper);
  }
  .call-to-action {
    position: absolute;
    left: 770px;
    width: 560px;
    top: 562px;
    margin: 0;
    text-align: center;
    font-size: 36px;
    font-weight: 400;
    line-height: 46px;
    color: var(--ink);
  }
  .call-to-action .web-address {
    font-weight: 700;
    color: var(--brand-blue);
  }
</style>
</head>
<body>
  <section class="billboard">
    <svg class="billboard-shapes" viewBox="0 0 1383 690" xmlns="http://www.w3.org/2000/svg">
      <defs>
        <clipPath id="photo-circle">
          <circle cx="1082" cy="320" r="445"/>
        </clipPath>
        <linearGradient id="photo-tone" x1="0" y1="0" x2="1" y2="1">
          <stop offset="0" stop-color="var(--photo-light)"/>
          <stop offset="0.45" stop-color="var(--photo-cool)"/>
          <stop offset="0.75" stop-color="var(--photo-mid)"/>
          <stop offset="1" stop-color="var(--photo-light)"/>
        </linearGradient>
      </defs>
      <rect class="band-white" x="0" y="0" width="1383" height="155" fill="var(--paper)"/>
      <rect class="band-black" x="0" y="155" width="1383" height="375" fill="var(--ink)"/>
      <rect class="band-blue" x="0" y="530" width="1383" height="160" fill="var(--brand-blue)"/>
      <circle class="circle-ring" cx="1082" cy="320" r="456" fill="var(--ink)"/>
      <g clip-path="url(#photo-circle)">
        <rect class="circle-base" x="0" y="0" width="1383" height="690" fill="var(--paper)"/>
        <rect class="photo-area" x="0" y="0" width="1383" height="529" fill="url(#photo-tone)"
              role="img" aria-label="Photo of a smiling support technician wearing a headset, typing on a laptop in a bright office"/>
        <line class="photo-rule" x1="600" y1="529.5" x2="1383" y2="529.5" stroke="var(--rule)" stroke-width="1.5"/>
      </g>
    </svg>

    <p class="brand-name">Brivoqua</p>

    <h1 class="headline">
      <span class="light">Seamless</span>
      <span class="bold">Technology</span>
      <span class="bold accent">Solutions</span>
      <span class="light">For Modern</span>
      <span class="bold">Businesses</span>
    </h1>

    <p class="tagline">Innovative IT and VOIP Solutions<br>Tailored for Your Business Success.</p>

    <p class="call-to-action">Transform Your Tech Today<br>at <span class="web-address">www.brivoqua.com</span></p>
  </section>
</body>
</html>
```